Heron Loan Partners Business Card

We need a business card design for our mortgage servicing company. In addition to servicing the loans of homeowners, we help homeowners with purchasing their homes and any mortgage refinancing. We would like to see designs that use the colors in the logo attached below (gold-ish yellow and navy blue), and any other design you deem fit! The design should communicate a Smart loans for an easier life provided by Heron.

```html
<!DOCTYPE html>
<html lang="en">
<head>
<meta charset="utf-8">
<title>Heron Loan Partners Business Card</title>
<link href="https://fonts.googleapis.com/css2?family=Arimo:ital,wght@0,400;0,700;1,400&display=swap" rel="stylesheet">
<style>
  :root {
    --gold: #cca23a;
    --navy: #1e1b4f;
    --paper: #f6f6f7;
    --white: #ffffff;
    --backdrop: #2a2a2c;
  }
  html, body {
    margin: 0;
    padding: 0;
    overflow: hidden;
  }
  body {
    width: 1200px;
    height: 960px;
    background: var(--backdrop);
    font-family: "Arimo", Arial, sans-serif;
    display: flex;
    flex-direction: column;
    align-items: center;
    justify-content: center;
    gap: 56px;
  }
  .card {
    position: relative;
    width: 700px;
    height: 400px;
    border-radius: 26px;
    overflow: hidden;
    background: var(--paper);
    box-shadow: 0 10px 30px rgba(0,0,0,0.45);
  }
  .card-back { background: var(--white); }
  .wordmark {
    position: absolute;
    display: flex;
    align-items: center;
    gap: 14px;
    color: var(--gold);
    font-weight: 700;
    white-space: nowrap;
  }
  .wordmark .mark-dot {
    border-radius: 50%;
    background: var(--navy);
    flex: none;
  }
  .card-back .wordmark {
    left: 50%;
    top: 50%;
    transform: translate(-50%, -50%);
    font-size: 46px;
  }
  .card-back .mark-dot { width: 26px; height: 26px; }

  .front-shapes { position: absolute; inset: 0; }
  .contact {
    position: absolute;
    left: 44px;
    top: 40px;
    color: var(--white);
  }
  .contact .name {
    color: var(--navy);
    font-weight: 700;
    font-size: 30px;
    margin: 0;
    line-height: 1.1;
  }
  .contact .role {
    font-style: italic;
    font-size: 19px;
    margin: 2px 0 20px;
  }
  .contact .address {
    font-size: 19px;
    line-height: 1.25;
    margin: 0 0 12px;
    font-style: normal;
  }
  .contact ul {
    list-style: none;
    margin: 0;
    padding: 0;
    font-size: 19px;
    line-height: 1.3;
  }
  .contact li { display: flex; align-items: center; gap: 8px; }
  .contact li svg { width: 15px; height: 15px; fill: var(--navy); flex: none; }
  .tagline {
    position: absolute;
    left: 44px;
    bottom: 44px;
    margin: 0;
    color: var(--white);
    font-size: 20px;
  }
  .card-front .wordmark {
    left: 440px;
    top: 200px;
    transform: translateY(-50%);
    font-size: 30px;
    flex-direction: column;
    align-items: flex-start;
    gap: 2px;
  }
  .card-front .wordmark span { display: flex; align-items: center; gap: 10px; }
  .card-front .mark-dot { width: 18px; height: 18px; }
</style>
</head>
<body>

  <section class="card card-back" aria-label="Card back">
    <div class="wordmark">
      <span class="mark-dot"></span>
      Heron Loan Partners
    </div>
  </section>

  <section class="card card-front" aria-label="Card front">
    <svg class="front-shapes" viewBox="0 0 700 400" preserveAspectRatio="none" aria-hidden="true">
      <polygon points="0,0 470,0 300,150 390,400 0,400" fill="var(--gold)"/>
      <polygon points="480,0 494,0 322,152 412,400 398,400 308,152" fill="var(--navy)"/>
    </svg>

    <div class="contact">
      <h1 class="name">Daniel Moreno</h1>
      <div class="role">President</div>
      <address class="address">4120 Harbor View Drive<br>Millbrook, NY 11020</address>
      <ul>
        <li>
          <svg viewBox="0 0 24 24"><path d="M6.6 10.8a15.1 15.1 0 0 0 6.6 6.6l2.2-2.2a1 1 0 0 1 1-.25 11.4 11.4 0 0 0 3.6.57 1 1 0 0 1 1 1V20a1 1 0 0 1-1 1A17 17 0 0 1 3 4a1 1 0 0 1 1-1h3.5a1 1 0 0 1 1 1c0 1.25.2 2.45.57 3.57a1 1 0 0 1-.25 1z"/></svg>
          (555) 0147-6180
        </li>
        <li>
          <svg viewBox="0 0 24 24"><path d="M2 5h20v14H2z"/><path d="M3 6l9 7 9-7" fill="none" stroke="var(--gold)" stroke-width="2"/></svg>
          name@heronloan.com
        </li>
        <li>
          <svg viewBox="0 0 24 24"><circle cx="12" cy="12" r="10"/></svg>
          www.heronloan.com
        </li>
      </ul>
    </div>

    <p class="tagline">Smart loans for an easier life</p>

    <div class="wordmark">
      <span><span class="mark-dot"></span>Heron Loan</span>
      <span>Partners</span>
    </div>
  </section>

</body>
</html>
```